Rehabilitation Centre Driving Evaluation brochure

I have already designed a brochure when I was at my previous workplace, but need a new one for my own rehab clinic. I will attach the brochure that I already did, as the information hasn't really changed. It is just very old and very ugly. It is an information pamphlet that will be in physician offices. Please let me know if you need anything else.

Target Market(s)

physicians, rehabilitation professionals, therapists, and individuals with medical conditions who want to return to driving

Industry/Entity Type

Medical

Requirements
Nice to have
• I am not stuck on the trifold, and actually may prefer a single fold brochure.

```html
<!DOCTYPE html>
<html lang="en">
<head>
<meta charset="utf-8">
<title>Driving Evaluation and Training Center – Brochure</title>
<link href="https://fonts.googleapis.com/css2?family=Montserrat:wght@400;500;600&family=Oswald:wght@700&display=swap" rel="stylesheet">
<style>
  :root{
    --bg:#d9d9db;
    --ink:#2b2b2b;
    --navy:#1d4a72;
    --navy-dark:#123350;
    --lime:#b5c41a;
    --black:#0f0f10;
    --white:#ffffff;
  }
  *{box-sizing:border-box;margin:0;padding:0}
  html,body{width:960px;height:1200px;overflow:hidden;background:var(--bg)}
  body{font-family:"Montserrat",sans-serif;color:var(--ink);position:relative}
  .spread{position:absolute;left:40px;width:880px;display:flex;box-shadow:0 10px 30px rgba(0,0,0,.25)}
  .cover{top:40px;height:520px}
  .inside{top:600px;height:560px;background:var(--white)}
  .page{width:440px;height:100%;position:relative;overflow:hidden}

  /* back cover */
  .back{background:linear-gradient(160deg,#1c2f40 0%,#111 35%,var(--black) 100%);color:var(--white);padding:50px 44px 30px}
  .back h2{font-weight:500;font-size:17px;color:var(--lime);margin-bottom:10px}
  .back p{font-size:10.5px;line-height:1.5;margin-bottom:10px;color:#e8e8e8}
  .brand{display:flex;align-items:center;gap:10px}
  .brand-dot{width:22px;height:22px;border-radius:50%;background:var(--lime);flex:none}
  .brand-name{font-size:17px;font-weight:500;line-height:1.15;color:var(--white)}
  .back .brand{margin-top:60px;margin-bottom:18px}
  .contact{list-style:none;font-size:11.5px;line-height:1.8}
  .contact li{display:flex;align-items:center;gap:10px}
  .contact svg{width:13px;height:13px;flex:none}

  /* front cover */
  .front{background:var(--black)}
  .front .photo{position:absolute;inset:0;background:linear-gradient(180deg,#e6e6e6 0%,#a9a9a9 30%,#5a5a5a 55%,#222 80%,#111 100%)}
  .front .brand{position:absolute;top:34px;left:34px}
  .front .brand-name{color:var(--navy-dark)}
  .title{position:absolute;left:34px;top:300px;font-family:"Oswald",sans-serif;font-size:34px;line-height:1.05;text-transform:uppercase;color:var(--white)}
  .title span{display:block;color:var(--lime)}
  .subtitle{position:absolute;left:34px;top:384px;font-size:13px;color:var(--white);letter-spacing:.5px}
  .url{position:absolute;left:34px;bottom:34px;font-size:10px;color:#bbb}

  /* inside */
  .band-top{position:absolute;top:0;left:0;right:0;height:50px;background:var(--navy)}
  .band-bottom{position:absolute;bottom:0;left:0;width:880px;height:18px;background:var(--navy)}
  .left-in{padding:15px 30px 26px}
  .left-in h2{position:relative;color:var(--white);font-weight:500;font-size:17px;margin:0 0 22px}
  .reason{display:flex;gap:14px}
  .emblem{width:64px;height:78px;flex:none;background:linear-gradient(180deg,#e5e5e5,#bdbdbd);border-radius:4px}
  .body{font-size:9px;line-height:1.4;color:var(--ink)}
  .body p{margin-bottom:6px}
  .eligibility{background:var(--lime);color:var(--white);border-radius:14px;padding:10px 18px;margin:8px 0 14px}
  .eligibility h3{font-weight:500;font-size:16px;margin-bottom:3px}
  .eligibility p{font-size:9px;line-height:1.4}
  .what h2{color:var(--navy);font-size:17px;font-weight:500;margin:0 0 6px}

  .right-in{background:linear-gradient(180deg,#fff 55%,#e4e7ea 100%)}
  .wheel-photo{position:absolute;top:0;left:20px;right:0;height:120px;background:linear-gradient(120deg,#c9b9a4 0%,#6c6c6c 40%,#2c2f33 100%);border-bottom-left-radius:26px}
  .components{position:absolute;top:134px;left:28px;right:28px}
  .components h2{color:var(--navy);font-weight:500;font-size:16px;margin-bottom:8px}
  .components h3{color:var(--navy);font-weight:600;font-size:11px;margin:8px 0 3px}
</style>
</head>
<body>

<section class="spread cover">
  <article class="page back">
    <h2>Referral Process</h2>
    <p>Referrals may be made by physicians, therapists, individuals requiring service, insurance companies, case managers, community service agencies, etc. The referral source will be asked to complete a referral form. The client’s physician will be contacted and asked to complete a medical referral form stating the client is medically able to participate in the assessment.</p>
    <p>Referrals can be made for any individual who requires an evaluation of their driving skills or adaptive equipment needs by contacting us.</p>
    <div class="brand">
      <span class="brand-dot"></span>
      <span class="brand-name">Northway<br>Rehabilitation Associates</span>
    </div>
    <ul class="contact">
      <li><svg viewBox="0 0 24 24" fill="none" stroke="#b5c41a" stroke-width="2"><path d="M12 22s7-7 7-12a7 7 0 0 0-14 0c0 5 7 12 7 12z"/><circle cx="12" cy="10" r="2.5"/></svg>420 Cedarline Road, Unit #5<br>Millbrook, Ontario, K0L 2P0</li>
      <li><svg viewBox="0 0 24 24" fill="#b5c41a"><path d="M6.6 10.8a15 15 0 0 0 6.6 6.6l2.2-2.2a1 1 0 0 1 1-.25 11 11 0 0 0 3.6.6 1 1 0 0 1 1 1V20a1 1 0 0 1-1 1A17 17 0 0 1 3 4a1 1 0 0 1 1-1h3.5a1 1 0 0 1 1 1 11 11 0 0 0 .6 3.6 1 1 0 0 1-.25 1z"/></svg>555 210 4470</li>
      <li><svg viewBox="0 0 24 24" fill="#b5c41a"><rect x="6" y="2" width="12" height="6"/><rect x="3" y="9" width="18" height="8" rx="1"/><rect x="6" y="14" width="12" height="8" fill="#fff"/></svg>555 210 4471</li>
      <li><svg viewBox="0 0 24 24" fill="none" stroke="#b5c41a" stroke-width="2"><rect x="3" y="5" width="18" height="14"/><path d="M3 5l9 8 9-8"/></svg>office@northwayrehab.ca</li>
      <li><svg viewBox="0 0 24 24" fill="none" stroke="#b5c41a" stroke-width="2"><circle cx="12" cy="12" r="9"/><path d="M3 12h18M12 3c3 3 3 15 0 18M12 3c-3 3-3 15 0 18"/></svg>www.northwayrehab.ca</li>
    </ul>
  </article>

  <article class="page front">
    <div class="photo" role="img" aria-label="Photograph of a car driving on a foggy forest road"></div>
    <div class="brand">
      <span class="brand-dot"></span>
      <span class="brand-name">Northway<br>Rehabilitation Associates</span>
    </div>
    <h1 class="title">Driving Evaluation<span>and Training Center</span></h1>
    <p class="subtitle">A comprehensive driver rehabilitation program</p>
    <p class="url">www.northwayrehab.ca</p>
  </article>
</section>

<section class="spread inside">
  <article class="page left-in">
    <div class="band-top"></div>
    <h2>Reason for Assesment</h2>
    <div class="reason">
      <div class="emblem" role="img" aria-label="Illustration of a medical caduceus emblem"></div>
      <div class="body">
        <p>Each physician is required by law to report to the Ministry of Transportation any individual whose driving skills may be affected as a result of illness or injury. Therefore, the client’s driver’s licence may be placed under medical suspension. If this occurs, the client will be asked to undergo a driving evaluation from an Ontario Driver Assessment Centre.</p>
        <p>Individuals affected by illness, injury, or the aging process, whose driving skills have the potential to be affected, are also encouraged to undergo an evaluation of driving skills. The evaluation is designed to assess each client’s ability to safely operate a motor vehicle and provide recommendations as needed.</p>
      </div>
    </div>
    <div class="eligibility">
      <h3>Eligibility</h3>
      <p>Most individuals with disabilities are eligible for an evaluation of their ability to drive. Clients must have a valid driver’s licence or the ability to obtain a temporary driver’s licence or learner’s permit.</p>
    </div>
    <div class="what body">
      <h2>What we do?</h2>
      <p>Northway Rehabilitation Associates is committed to providing optimal rehabilitation service in a cost effective manner.</p>
      <p>We offer a multi-disciplinary, client-centred program of assessment, treatment and consultation for clients with physical, cognitive and/or perceptual impairments. We are aware each client is unique, therefore each program is tailored according to the individual’s needs and personal goals.</p>
      <p>The driving assessment and training program is part of our comprehensive rehabilitation services. It is a service which represents our dedication to assist all individuals achieve optimal independence. Driving is an integral skill which is often essential for independence in the community.</p>
    </div>
  </article>

  <article class="page right-in">
    <div class="wheel-photo" role="img" aria-label="Photograph of hands on a car steering wheel"></div>
    <div class="components body">
      <h2>Program Components &amp; Services</h2>
      <h3>Clinical Evaluation</h3>
      <p>The client is assessed by a certified occupational therapist. The client is initially seen in clinic for an assessment of physical, cognitive, and perceptual functioning as they relate to driving. The in-clinic portion of the assessment provides the therapist with information regarding medical history, driving history, knowledge of road signs and driving rules, physical abilities, cognitive status, visual and perceptual skills.</p>
      <h3>On the Road Evaluation</h3>
      <p>Following the in-clinic assessment, each client is then assessed in car by the therapist together with a certified driving instructor. The in-car portion of the evaluation provides valuable information regarding the individual’s functional driving skills.</p>
      <h3>Evaluation Equipment Needs</h3>
      <p>During the evaluation, it will be determined whether adaptive equipment will be necessary to improve the client’s ability to drive safely. Recommendations will be made for adaptive equipment and installation.</p>
      <h3>Training &amp; Follow-up Services</h3>
      <p>Clients are commonly seen following a driving evaluation for training with driving skills or adaptive equipment. Further involvement with the occupational therapist may be indicated for cognitive or perceptual retraining, mobility-aid prescription, vehicle modification, or consultation with appropriate new vehicle purchase.</p>
    </div>
  </article>
  <div class="band-bottom"></div>
</section>

</body>
</html>
```